KBT Business Cards

We require business cards for our business. We would like a matte black back to the card, with our logo centred in the middle. The front side of the card is open to design.

Target Market(s)

Clients looking for legal services (professional)

Industry/Entity Type

Legal

Contact Information for Business Card

Doran Kelbrath
Partner
Mobile: 0461 738 524
Email: doran@kbtlaw.co
Website: www.kbtlaw.co
Level 3, 118 Wendmore Street
Sydney NSW 2000

Font styles to use
Other font styles liked:
• Avenir

Colors
f04a50
ffffff
1b1b1b

Requirements
Must have
• Black back with logo included in the centre of the card.
• Our font is Avenir.

```html
<!DOCTYPE html>
<html lang="en">
<head>
<meta charset="utf-8">
<title>KBT Law Business Cards</title>
<link href="https://fonts.googleapis.com/css2?family=Roboto:wght@400;500&display=swap" rel="stylesheet">
<style>
  :root {
    --backdrop: #e4e4e4;
    --paper: #ffffff;
    --ink: #1b1b1b;
    --ink-soft: #555555;
    --crimson: #d0234b;
    --crimson-deep: #9c1c37;
    --matte: #231f20;
  }
  * { box-sizing: border-box; margin: 0; padding: 0; }
  html, body {
    width: 1125px; height: 1200px; overflow: hidden;
    background: var(--backdrop);
    font-family: "Roboto", Arial, sans-serif;
  }
  .card {
    position: absolute; left: 171px; width: 826px; height: 472px;
  }
  .card--front { top: 106px; background: var(--paper); }
  .card--back { top: 639px; background: var(--matte); }

  .brand {
    position: absolute; left: 55px; top: 92px;
    display: flex; align-items: center; gap: 26px;
  }
  .brand__square { width: 58px; height: 58px; background: var(--crimson); }
  .brand__name {
    font-size: 46px; font-weight: 500; color: var(--ink); letter-spacing: 1px;
  }

  .address {
    position: absolute; left: 52px; top: 282px;
    font-size: 19px; line-height: 25px; color: var(--ink-soft);
  }
  .contacts {
    position: absolute; left: 52px; top: 346px; list-style: none;
    font-size: 19px; color: var(--ink-soft);
  }
  .contacts li { display: flex; align-items: center; height: 26px; }
  .contacts svg { width: 18px; height: 18px; margin-right: 14px; fill: var(--crimson); }

  .person {
    position: absolute; right: 52px; top: 325px; text-align: right;
  }
  .person__name { font-size: 31px; font-weight: 500; color: var(--crimson); line-height: 1.1; }
  .person__role { font-size: 19px; font-weight: 500; color: var(--ink); margin-top: 2px; }

  .base-band {
    position: absolute; left: 0; bottom: 0; width: 100%; height: 11px;
    display: flex; gap: 3px; background: var(--paper);
  }
  .base-band span {
    flex: 1; background: linear-gradient(90deg, var(--crimson-deep), var(--crimson));
  }

  .back-brand {
    position: absolute; left: 0; right: 0; top: 198px;
    display: flex; justify-content: center; align-items: center; gap: 24px;
  }
  .back-brand__square { width: 54px; height: 54px; background: var(--crimson); }
  .back-brand__name { font-size: 52px; font-weight: 500; color: var(--paper); letter-spacing: 2px; }

  .back-web {
    position: absolute; left: 0; right: 0; top: 398px; text-align: center;
    font-size: 17px; color: var(--paper); letter-spacing: 14px; padding-left: 14px;
  }
</style>
</head>
<body>
  <section class="card card--front">
    <div class="brand">
      <div class="brand__square"></div>
      <div class="brand__name">KBT LAW</div>
    </div>

    <p class="address">Level 3, 118 Wendmore<br>Street, Sydney NSW 2000</p>

    <ul class="contacts">
      <li>
        <svg viewBox="0 0 18 18"><path d="M5 0h8a1.5 1.5 0 0 1 1.5 1.5v15A1.5 1.5 0 0 1 13 18H5a1.5 1.5 0 0 1-1.5-1.5v-15A1.5 1.5 0 0 1 5 0zm.5 2v12h7V2zm3.5 13.2a1 1 0 1 0 0 .1z"/></svg>
        0461 738 524
      </li>
      <li>
        <svg viewBox="0 0 18 18"><path d="M1 5h16v10H1zm1.5 1.5v.3L9 11l6.5-4.2v-.3z"/></svg>
        doran@kbtlaw.co
      </li>
      <li>
        <svg viewBox="0 0 18 18"><circle cx="9" cy="9" r="8.5"/><path d="M4 5c2 0 3 1 3 3s-2 2-2 4M11 2c0 2 2 2 3 3s0 3-2 3-2 2-1 4" stroke="#fff" stroke-width="1.6" fill="none"/></svg>
        www.kbtlaw.co
      </li>
    </ul>

    <div class="person">
      <div class="person__name">Doran Kelbrath</div>
      <div class="person__role">Partner</div>
    </div>

    <div class="base-band"><span></span><span></span><span></span><span></span><span></span></div>
  </section>

  <section class="card card--back">
    <div class="back-brand">
      <div class="back-brand__square"></div>
      <div class="back-brand__name">KBT LAW</div>
    </div>
    <div class="back-web">WWW.KBTLAW.CO</div>
  </section>
</body>
</html>
```